Flat bootstrap design for existing site

I'm looking for a modern flat design based around an existing logo. This has to be a custom design (no external templates), and implemented into a bootstrap framework.

The logo is attached as 2 versions - choose whichever you want, that flows better with whatever design you choose.

Added screenshots of the existing site (currently using the default bootstrap layouts). Please make your designs around those pages in the screenshots (i.e. the homepage only has the postal code input and the header). The active page has 3 screenshots, because I wanted to illustrate the other states that would be visible (in the table rows).

This is a moving/junk removal website, just for some context.

Here's some example websites (flat designs) that I like, just to give you an idea of what I'm after.

https://www.plimvora.com/
https://dacklow.com/
https://trevanu.com/
https://quobrintal.com/en/

Coding

Coded - Design and coding required

Number of Pages Required

5+ page

Colors

Designer to choose colors to be used in the design.

Requirements
Must have
• It must be a modern/simple flat design, that is built around the existing logo (attached).
• It has to be implemented using bootstrap.

```html
<!DOCTYPE html>
<html lang="en">
<head>
<meta charset="utf-8">
<title>Haulix – Junk Removal</title>
<link href="https://fonts.googleapis.com/css2?family=Lato:wght@400;700;900&display=swap" rel="stylesheet">
<style>
  :root {
    --header-blue: #3ccdfe;
    --hero-blue: #5bd6ff;
    --logo-tile: #55d3fd;
    --white: #ffffff;
    --ink: #0e0e0e;
    --accent-orange: #f26a21;
    --placeholder: #3aa6d8;
    --art-light: #7fdfff;
    --art-dark: #4ac4ee;
  }
  * { margin: 0; padding: 0; box-sizing: border-box; }
  html, body { width: 1200px; height: 778px; overflow: hidden; }
  body {
    font-family: "Lato", sans-serif;
    background: var(--hero-blue);
    position: relative;
    color: var(--white);
  }
  .site-header {
    position: absolute; left: 0; top: 0;
    width: 1200px; height: 89px;
    background: var(--header-blue);
  }
  .brand {
    position: absolute; left: 79px; top: 0;
    width: 177px; height: 89px;
    background: var(--logo-tile);
    display: flex; align-items: center; justify-content: center; gap: 8px;
    font-weight: 900; font-size: 27px; letter-spacing: 1px;
    color: var(--white); text-decoration: none;
  }
  .brand-dot {
    width: 12px; height: 12px; border-radius: 50%; background: var(--white);
  }
  .main-nav {
    position: absolute; top: 31px; left: 600px;
    display: flex; align-items: center;
  }
  .nav-link {
    font-weight: 700; font-size: 15.5px; color: var(--white);
    text-decoration: none; text-transform: uppercase;
    height: 31px; line-height: 31px;
  }
  .nav-link.is-active {
    border: 2px solid var(--white); padding: 0 9px; line-height: 27px;
    position: relative;
  }
  .nav-link + .nav-link { margin-left: 33px; }
  .cursor {
    position: absolute; left: 58px; top: 16px; width: 22px; height: 24px;
  }
  .hero-art {
    position: absolute; left: 617px; top: 194px;
    width: 494px; height: 584px;
    background: radial-gradient(ellipse at 50% 40%, var(--art-light) 0%, var(--art-dark) 60%, var(--hero-blue) 100%);
    opacity: 0.55;
    border-radius: 40px 40px 0 0;
  }
  .hero-title {
    position: absolute; left: 0; top: 300px; width: 1200px;
    text-align: center;
    font-weight: 900; font-size: 51px; line-height: 62px;
    text-transform: uppercase;
  }
  .tag {
    display: inline-block;
    background: var(--ink); color: var(--header-blue);
    font-weight: 700;
    padding: 4px 16px;
    transform: rotate(-10deg);
    margin: 0 10px;
  }
  .booking-form {
    position: absolute; left: 404px; top: 439px;
    display: flex; gap: 7px;
  }
  .postal-input {
    width: 252px; height: 41px;
    border: 2px solid var(--white); border-radius: 3px;
    background: transparent;
    font-family: "Lato", sans-serif; font-weight: 700; font-size: 14px;
    color: var(--placeholder); padding: 0 14px; line-height: 37px;
  }
  .book-button {
    width: 131px; height: 41px;
    background: var(--accent-orange); color: var(--white);
    border: none; border-radius: 2px;
    font-family: "Lato", sans-serif; font-weight: 700; font-size: 15.5px;
    text-transform: uppercase;
  }
</style>
</head>
<body>
  <header class="site-header">
    <a class="brand" href="#"><span class="brand-dot"></span>HAULIX</a>
    <nav class="main-nav">
      <a class="nav-link is-active" href="#">Book
        <svg class="cursor" viewBox="0 0 22 24"><path d="M2 2 L20 12 L12 14 L9 22 Z" fill="#fff"/></svg>
      </a>
      <a class="nav-link" href="#">How it works</a>
      <a class="nav-link" href="#">Become a driver</a>
      <a class="nav-link" href="#">Login</a>
    </nav>
  </header>

  <div class="hero-art" role="img" aria-label="Open cardboard box full of old appliances and household junk"></div>

  <h1 class="hero-title">Need a <span class="tag">Junk</span> removed?</h1>

  <form class="booking-form">
    <div class="postal-input">Enter your postal code here</div>
    <button class="book-button" type="button">Book now!</button>
  </form>
</body>
</html>
```